Webdesign für Steuerberaterin
Zielgruppe
Ich bin Steuerberaterin. Meine Zielgruppe sind sowohl Privatpersonen als auch Unternehmer sowie Männer und Frauen.
Aufgabenstellung
Bitte mein Logo und Foto mit berücksichtigen. Ich möchte keine Website, auf der alle 'Reiter' als eine Seite von oben nach unten durchlaufen. Sondern wirklich einzelne, voneinander getrennte Seiten.

```html
<!DOCTYPE html>
<html lang="de">
<head>
<meta charset="utf-8">
<title>Maren Brodtke – Steuerberaterin</title>
<link href="https://fonts.googleapis.com/css2?family=Cormorant+Garamond:wght@500&family=PT+Sans:wght@400;700&family=Carlito&display=swap" rel="stylesheet">
<style>
  :root {
    --sidebar: #1f252d;
    --gold: #c39429;
    --gold-heading: #a8822a;
    --gold-rule: #c9a232;
    --band: #dcb73d;
    --text: #4a4a4a;
    --page: #ffffff;
  }
  * { margin: 0; padding: 0; box-sizing: border-box; }
  html, body { width: 1200px; height: 768px; overflow: hidden; background: var(--page); }
  body { position: relative; font-family: "PT Sans", sans-serif; color: var(--text); }

  .sidebar { position: absolute; left: 0; top: 0; width: 307px; height: 744px; background: var(--sidebar); overflow: hidden; }
  .sidebar-emblem {
    position: absolute; left: -20px; top: 312px; width: 145px; height: 430px;
    border-radius: 0 70px 70px 0;
    background: linear-gradient(180deg, #8c8676 0%, #d9d5c9 45%, #f5f1e6 60%, #9b9482 100%);
    opacity: .85;
  }
  .main-nav { position: absolute; left: 80px; top: 180px; font-family: "Carlito", sans-serif; font-size: 13.5px; }
  .main-nav a { display: block; color: var(--gold); text-decoration: none; margin-bottom: 26px; line-height: 18px; }

  .brand { position: absolute; left: 350px; top: 50px; width: 184px; text-align: center; }
  .brand-mark { width: 34px; height: 34px; border-radius: 50%; background: var(--gold); margin: 0 auto 12px; }
  .brand-name { font-family: "PT Sans", sans-serif; font-size: 20px; font-weight: 400; color: var(--gold); }

  .portrait {
    position: absolute; left: 194px; top: 186px; width: 455px; height: 331px;
    background: radial-gradient(ellipse at 50% 45%, #f6f6f7 0%, #e4e4e6 55%, #c9c9cc 100%);
  }

  .welcome { position: absolute; left: 691px; top: 130px; width: 473px; text-align: center; }
  .welcome-title { font-family: "Cormorant Garamond", serif; font-weight: 500; font-size: 27px; color: var(--gold-heading); line-height: 44px; }
  .welcome-rule { height: 2px; background: var(--gold-rule); margin-top: 14px; }
  .welcome-lead { font-weight: 700; font-size: 14px; margin-top: 32px; line-height: 18px; }
  .welcome-text { font-size: 13.5px; line-height: 17px; margin-top: 21px; }

  .footer-band { position: absolute; left: 0; bottom: 0; width: 1200px; height: 24px; background: var(--band); }
  .footer-links { position: absolute; left: 81px; top: 3px; font-family: "Carlito", sans-serif; font-size: 13px; color: #2b2b2b; }
  .footer-links a { color: inherit; text-decoration: none; }
  .footer-links span { margin: 0 7px; }
</style>
</head>
<body>
  <aside class="sidebar">
    <div class="sidebar-emblem" role="img" aria-label="Großes dekoratives Paragraphenzeichen in Champagnertönen"></div>
    <nav class="main-nav">
      <a href="#">Über mich</a>
      <a href="#">Leistungen</a>
      <a href="#">Kontakt</a>
    </nav>
  </aside>

  <div class="brand">
    <div class="brand-mark"></div>
    <div class="brand-name">Maren Brodtke</div>
  </div>

  <div class="portrait" role="img" aria-label="Porträtfoto der Steuerberaterin vor heller Steinwand"></div>

  <section class="welcome">
    <h1 class="welcome-title">Schön, dass Sie da sind</h1>
    <div class="welcome-rule"></div>
    <p class="welcome-lead">Ich freue mich, dass Sie den Weg zu mir gefunden haben!</p>
    <p class="welcome-text">Sie sind bei mir genau richtig:<br>Egal, ob Sie Privatperson sind, die Ihre Einkommensteuer-Erklärung<br>in vertrauensvolle Hände geben möchte,<br>oder Unternehmer, der sich z.B. das „Rundum-Sorglos-Paket“<br>mit Buchführung, Jahresabschluss und Steuererklärungen wünscht.</p>
    <p class="welcome-text">Schauen Sie sich hier gerne um und melden Sie sich bei mir<br>– ich bin bei jedem steuerlichen Thema<br>gerne Ihr kompetenter und zuverlässiger Ansprechpartner.</p>
    <p class="welcome-text">Für mich ist es eine Selbstverständlichkeit,<br>dass ich auch nach mehr als 12 Jahren Berufserfahrung<br>durch permanente Fortbildungen immer auf dem aktuellsten Stand<br>der relevanten Gesetze und Verordnungen bin.<br>Nur so kann ich Sie bestmöglich beraten.</p>
  </section>

  <footer class="footer-band">
    <div class="footer-links"><a href="#">Impressum</a><span>|</span><a href="#">Datenschutz</a></div>
  </footer>
</body>
</html>
```